Alaska Law Firm Needs a Sticker Design

We need a design for stickers to put on already-printed brochures. We mail the brochures to potential clients so they can learn more about accident-induced injuries, insurance claims, legal representation, and our own law firm.

One of our lawyers wrote a book that provides a helpful overview of personal injury claims. We are offering this book for free to anyone who calls and requests it. Therefore, the sticker design should include one of the following phrases, or something very similar:
a) "Still have questions? Call and request our book-- for free!"
b) "Still have questions about auto accident claims? Call and request our book today."
c) "Still have questions about filing a claim? Call and request a free copy of our book."
d) "Still have questions? Call us today to request a free copy of our book, Clear Lanes Ahead."
e) "To learn more about automobile accidents and insurance, call today and request a free copy of our book."

The sticker should be approximately 3"x3" and may be a circle, square, rectangle, or ellipsis. The sticker will be placed on the back of the folder, which is light blue. We would like the sticker to match the color scheme of our website and the folder.

I will upload an image of the book cover as soon as I obtain it.

Law Firm

Font styles to use
Serif
Sans Serif

Requirements
Should not have
• Bright colors that aren't already used in the folder design. e.g. no bright orange, pink, chartreuse, turquoise, yellow, red.

```html
<!DOCTYPE html>
<html lang="en">
<head>
<meta charset="utf-8">
<title>Book Offer Stickers</title>
<link rel="stylesheet" href="https://fonts.googleapis.com/css2?family=Arimo:ital,wght@0,400;0,700;1,400;1,700&family=Oswald:wght@700&display=swap">
<style>
  :root {
    --page-bg: #ffffff;
    --blue-deep: #0c3a62;
    --blue-mid: #1b5f96;
    --blue-glow: #3a8fcb;
    --band-grey: #4b4a4f;
    --band-line: #8fa9c2;
    --ink-white: #ffffff;
    --art-light: #dfe7ef;
    --art-mid: #b9c7d4;
    --cover-tone: #5d7d98;
  }
  html, body {
    margin: 0;
    width: 1200px;
    height: 800px;
    overflow: hidden;
    background: var(--page-bg);
  }
  .sheet {
    position: relative;
    width: 1200px;
    height: 800px;
  }
  .sticker {
    position: absolute;
    width: 342px;
    height: 342px;
  }
  .sticker svg { display: block; width: 342px; height: 342px; }
  .lead {
    font-family: "Arimo", Arial, sans-serif;
    font-size: 21px;
    fill: var(--ink-white);
  }
  .headline {
    font-family: "Oswald", "Arial Narrow", sans-serif;
    font-weight: 700;
    font-size: 42px;
    fill: var(--ink-white);
  }
  .qmark {
    font-family: "Oswald", "Arial Narrow", sans-serif;
    font-weight: 700;
    fill: var(--blue-deep);
  }
  .band-call {
    font-family: "Arimo", Arial, sans-serif;
    font-weight: 700;
    font-size: 17px;
    fill: var(--ink-white);
  }
  .band-offer {
    font-family: "Arimo", Arial, sans-serif;
    font-style: italic;
    font-size: 22px;
    fill: var(--ink-white);
  }
  .band-offer .strong { font-weight: 700; }
  .band-small {
    font-family: "Arimo", Arial, sans-serif;
    font-size: 16px;
    fill: var(--ink-white);
  }
  .band-small .strong { font-weight: 700; font-style: italic; }
  .band-small .soft { font-style: italic; }
</style>
</head>
<body>
<svg width="0" height="0" style="position:absolute" aria-hidden="true">
  <defs>
    <radialGradient id="sticker-glow" cx="50%" cy="80%" r="75%">
      <stop offset="0" stop-color="var(--blue-glow)"/>
      <stop offset="0.55" stop-color="var(--blue-mid)"/>
      <stop offset="1" stop-color="var(--blue-deep)"/>
    </radialGradient>
    <linearGradient id="cover-fill" x1="0" y1="0" x2="0" y2="1">
      <stop offset="0" stop-color="#e9eef3"/>
      <stop offset="0.3" stop-color="var(--cover-tone)"/>
      <stop offset="1" stop-color="#3f5a44"/>
    </linearGradient>
    <linearGradient id="art-fill" x1="0" y1="0" x2="0" y2="1">
      <stop offset="0" stop-color="var(--art-light)"/>
      <stop offset="1" stop-color="var(--art-mid)"/>
    </linearGradient>
  </defs>
</svg>

<main class="sheet">

  <!-- Sticker 1 -->
  <section class="sticker" style="left:29px;top:29px">
    <svg viewBox="0 0 342 342">
      <rect width="342" height="342" rx="13" fill="url(#sticker-glow)"/>
      <text class="lead" x="171" y="63" text-anchor="middle">Still Have</text>
      <text class="headline" x="171" y="110" text-anchor="middle" textLength="157" lengthAdjust="spacingAndGlyphs">Questions</text>
      <circle cx="171" cy="186" r="56" fill="var(--ink-white)"/>
      <text class="qmark" x="171" y="221" font-size="98" text-anchor="middle">?</text>
      <path d="M0 269 H342 V329 a13 13 0 0 1 -13 13 H13 a13 13 0 0 1 -13 -13 Z" fill="var(--band-grey)"/>
      <line x1="0" y1="269" x2="342" y2="269" stroke="var(--band-line)" stroke-width="1.5"/>
      <text class="band-call" x="25" y="292" textLength="174" lengthAdjust="spacingAndGlyphs">Call And Request Our</text>
      <text class="band-offer" x="25" y="318" textLength="176" lengthAdjust="spacingAndGlyphs"><tspan class="strong">BOOK</tspan> for <tspan class="strong">FREE!</tspan></text>
      <path d="M206 316 Q232 314 246 294" fill="none" stroke="var(--ink-white)" stroke-width="2.5"/>
      <polygon points="252,286 248,300 239,293" fill="var(--ink-white)"/>
      <rect x="257" y="245" width="66" height="80" transform="rotate(10 290 285)" fill="url(#cover-fill)" stroke="#ffffff" stroke-width="2" role="img" aria-label="Book cover of the firm's free guide"/>
    </svg>
  </section>

  <!-- Sticker 2 -->
  <section class="sticker" style="left:429px;top:29px">
    <svg viewBox="0 0 342 342">
      <rect width="342" height="342" rx="13" fill="url(#sticker-glow)"/>
      <text class="lead" x="171" y="37" text-anchor="middle">Still Have Questions</text>
      <text class="lead" x="171" y="63" text-anchor="middle">About Auto Accident</text>
      <text class="headline" x="160" y="110" text-anchor="middle" textLength="106" lengthAdjust="spacingAndGlyphs">Claims</text>
      <circle cx="247" cy="95" r="26" fill="var(--ink-white)"/>
      <text class="qmark" x="247" y="111" font-size="44" text-anchor="middle">?</text>
      <rect x="61" y="127" width="221" height="108" rx="10" fill="url(#art-fill)" opacity="0.85" role="img" aria-label="Illustration of two cars colliding head-on"/>
      <path d="M0 269 H342 V329 a13 13 0 0 1 -13 13 H13 a13 13 0 0 1 -13 -13 Z" fill="var(--band-grey)"/>
      <line x1="0" y1="269" x2="342" y2="269" stroke="var(--band-line)" stroke-width="1.5"/>
      <text class="band-call" x="25" y="292" textLength="174" lengthAdjust="spacingAndGlyphs">Call And Request Our</text>
      <text class="band-offer" x="25" y="318" textLength="176" lengthAdjust="spacingAndGlyphs"><tspan class="strong">BOOK</tspan> for <tspan class="strong">FREE!</tspan></text>
      <path d="M206 316 Q232 314 246 294" fill="none" stroke="var(--ink-white)" stroke-width="2.5"/>
      <polygon points="252,286 248,300 239,293" fill="var(--ink-white)"/>
      <rect x="257" y="245" width="66" height="80" transform="rotate(10 290 285)" fill="url(#cover-fill)" stroke="#ffffff" stroke-width="2" role="img" aria-label="Book cover of the firm's free guide"/>
    </svg>
  </section>

  <!-- Sticker 3 -->
  <section class="sticker" style="left:829px;top:29px">
    <svg viewBox="0 0 342 342">
      <rect width="342" height="342" rx="13" fill="url(#sticker-glow)"/>
      <text class="lead" x="171" y="37" text-anchor="middle">Still Have Questions</text>
      <text class="lead" x="171" y="63" text-anchor="middle">About Filing a</text>
      <text class="headline" x="161" y="110" text-anchor="middle" textLength="108" lengthAdjust="spacingAndGlyphs">Claims</text>
      <rect x="123" y="127" width="143" height="123" rx="8" fill="url(#art-fill)" opacity="0.85" role="img" aria-label="Illustration of a claim form with a question mark and a pencil"/>
      <path d="M0 269 H342 V329 a13 13 0 0 1 -13 13 H13 a13 13 0 0 1 -13 -13 Z" fill="var(--band-grey)"/>
      <line x1="0" y1="269" x2="342" y2="269" stroke="var(--band-line)" stroke-width="1.5"/>
      <text class="band-call" x="25" y="292" textLength="174" lengthAdjust="spacingAndGlyphs">Call And Request Our</text>
      <text class="band-offer" x="25" y="318" textLength="176" lengthAdjust="spacingAndGlyphs"><tspan class="strong">BOOK</tspan> for <tspan class="strong">FREE!</tspan></text>
      <path d="M206 316 Q232 314 246 294" fill="none" stroke="var(--ink-white)" stroke-width="2.5"/>
      <polygon points="252,286 248,300 239,293" fill="var(--ink-white)"/>
      <rect x="257" y="245" width="66" height="80" transform="rotate(10 290 285)" fill="url(#cover-fill)" stroke="#ffffff" stroke-width="2" role="img" aria-label="Book cover of the firm's free guide"/>
    </svg>
  </section>

  <!-- Sticker 4 -->
  <section class="sticker" style="left:29px;top:429px">
    <svg viewBox="0 0 342 342">
      <rect width="342" height="342" rx="13" fill="url(#sticker-glow)"/>
      <text class="lead" x="171" y="63" text-anchor="middle">Still Have</text>
      <text class="headline" x="171" y="110" text-anchor="middle" textLength="157" lengthAdjust="spacingAndGlyphs">Questions</text>
      <circle cx="171" cy="186" r="56" fill="var(--ink-white)"/>
      <text class="qmark" x="171" y="221" font-size="98" text-anchor="middle">?</text>
      <path d="M0 252 H342 V329 a13 13 0 0 1 -13 13 H13 a13 13 0 0 1 -13 -13 Z" fill="var(--band-grey)"/>
      <line x1="0" y1="252" x2="342" y2="252" stroke="var(--band-line)" stroke-width="1.5"/>
      <text class="band-small" x="25" y="273">Call Us Today To Request</text>
      <text class="band-small" x="27" y="295"><tspan class="strong">A FREE COPY</tspan><tspan class="soft"> Of Our </tspan><tspan class="strong">BOOK</tspan>,</text>
      <text class="band-small" x="25" y="316">Clear Lanes Ahead.</text>
      <path d="M172 314 Q215 317 240 306" fill="none" stroke="var(--ink-white)" stroke-width="2.5"/>
      <polygon points="249,300 239,313 234,303" fill="var(--ink-white)"/>
      <rect x="257" y="245" width="66" height="80" transform="rotate(10 290 285)" fill="url(#cover-fill)" stroke="#ffffff" stroke-width="2" role="img" aria-label="Book cover of the firm's free guide"/>
    </svg>
  </section>

  <!-- Sticker 5 -->
  <section class="sticker" style="left:429px;top:429px">
    <svg viewBox="0 0 342 342">
      <rect width="342" height="342" rx="13" fill="url(#sticker-glow)"/>
      <text class="lead" x="171" y="37" text-anchor="middle">To Learn More About</text>
      <text class="lead" x="171" y="63" text-anchor="middle">Automobile Accidents And</text>
      <text class="headline" x="164" y="110" text-anchor="middle" textLength="150" lengthAdjust="spacingAndGlyphs">Insurance</text>
      <circle cx="270" cy="95" r="26" fill="var(--ink-white)"/>
      <text class="qmark" x="270" y="111" font-size="44" text-anchor="middle">?</text>
      <rect x="74" y="123" width="195" height="117" rx="10" fill="url(#art-fill)" opacity="0.85" role="img" aria-label="Illustration of a car crash"/>
      <path d="M0 270 H342 V329 a13 13 0 0 1 -13 13 H13 a13 13 0 0 1 -13 -13 Z" fill="var(--band-grey)"/>
      <line x1="0" y1="270" x2="342" y2="270" stroke="var(--band-line)" stroke-width="1.5"/>
      <text class="band-call" x="25" y="293" textLength="174" lengthAdjust="spacingAndGlyphs">Call And Request Our</text>
      <text class="band-offer" x="25" y="319" textLength="176" lengthAdjust="spacingAndGlyphs"><tspan class="strong">BOOK</tspan> for <tspan class="strong">FREE!</tspan></text>
      <path d="M206 316 Q232 314 246 294" fill="none" stroke="var(--ink-white)" stroke-width="2.5"/>
      <polygon points="252,286 248,300 239,293" fill="var(--ink-white)"/>
      <rect x="257" y="245" width="66" height="80" transform="rotate(10 290 285)" fill="url(#cover-fill)" stroke="#ffffff" stroke-width="2" role="img" aria-label="Book cover of the firm's free guide"/>
    </svg>
  </section>

  <!-- Sticker 6 -->
  <section class="sticker" style="left:829px;top:429px">
    <svg viewBox="0 0 342 342">
      <rect width="342" height="342" rx="13" fill="url(#sticker-glow)"/>
      <text class="lead" x="171" y="64" text-anchor="middle">Still Have Questions</text>
      <text class="lead" x="171" y="90" text-anchor="middle">About Filing a</text>
      <rect x="63" y="111" width="212" height="92" rx="6" fill="url(#art-fill)" opacity="0.85" transform="rotate(-4 169 157)" role="img" aria-label="Rubber stamp reading CLAIM"/>
      <circle cx="294" cy="186" r="26" fill="var(--ink-white)"/>
      <text class="qmark" x="294" y="202" font-size="44" text-anchor="middle">?</text>
      <path d="M0 270 H342 V329 a13 13 0 0 1 -13 13 H13 a13 13 0 0 1 -13 -13 Z" fill="var(--band-grey)"/>
      <line x1="0" y1="270" x2="342" y2="270" stroke="var(--band-line)" stroke-width="1.5"/>
      <text class="band-call" x="25" y="293" textLength="174" lengthAdjust="spacingAndGlyphs">Call And Request Our</text>
      <text class="band-offer" x="25" y="319" textLength="176" lengthAdjust="spacingAndGlyphs"><tspan class="strong">BOOK</tspan> for <tspan class="strong">FREE!</tspan></text>
      <path d="M206 316 Q232 314 246 294" fill="none" stroke="var(--ink-white)" stroke-width="2.5"/>
      <polygon points="252,286 248,300 239,293" fill="var(--ink-white)"/>
      <rect x="257" y="245" width="66" height="80" transform="rotate(10 290 285)" fill="url(#cover-fill)" stroke="#ffffff" stroke-width="2" role="img" aria-label="Book cover of the firm's free guide"/>
    </svg>
  </section>

</main>
</body>
</html>
```